Step and Repeat Backdrop for wedding reception photo booth

Would like to have a Step and Repeat Backdrop (8 foot high by 10 foot wide) that incorporates the wedding logo (attached) and the names Helen and Gavin. Background should be white, and wedding colors are burgundy and gold. Show me creativity :-) I have included some random samples.

```html
<!DOCTYPE html>
<html lang="en">
<head>
<meta charset="utf-8">
<title>Helen &amp; Gavin — Step and Repeat Backdrop</title>
<link href="https://fonts.googleapis.com/css2?family=Marcellus&display=swap" rel="stylesheet">
<style>
  :root {
    --backdrop-white: #ffffff;
    --burgundy: #7a1420;
    --rose-copper: #b77a6c;
    --stage-grey: #ecebe9;
  }
  html, body {
    margin: 0;
    padding: 0;
    width: 1200px;
    height: 900px;
    overflow: hidden;
    background: var(--stage-grey);
  }
  .backdrop {
    box-sizing: border-box;
    width: 1200px;
    height: 900px;
    padding: 28px 36px;
    background: var(--backdrop-white);
    display: grid;
    grid-template-columns: repeat(6, 1fr);
    grid-template-rows: repeat(5, 1fr);
    place-items: center;
    font-family: "Marcellus", "Times New Roman", serif;
  }
  .name-tile {
    width: 132px;
    height: 132px;
    border: 1.5px solid var(--rose-copper);
    border-radius: 50%;
    display: flex;
    flex-direction: column;
    align-items: center;
    justify-content: center;
    color: var(--rose-copper);
    font-size: 17px;
    letter-spacing: 0.06em;
    line-height: 1.25;
    text-transform: uppercase;
    text-align: center;
  }
  .hero-name {
    grid-column: 3 / 5;
    grid-row: 2 / 4;
    width: 330px;
    height: 330px;
    border: 3px solid var(--burgundy);
    border-radius: 50%;
    display: flex;
    flex-direction: column;
    align-items: center;
    justify-content: center;
    color: var(--burgundy);
    font-size: 42px;
    letter-spacing: 0.06em;
    line-height: 1.25;
    text-transform: uppercase;
    text-align: center;
  }
</style>
</head>
<body>
<main class="backdrop" aria-label="Helen and Gavin wedding step and repeat backdrop">
  <div class="name-tile"><span>Helen</span><span>&amp; Gavin</span></div>
  <div class="name-tile"><span>Helen</span><span>&amp; Gavin</span></div>
  <div class="name-tile"><span>Helen</span><span>&amp; Gavin</span></div>
  <div class="name-tile"><span>Helen</span><span>&amp; Gavin</span></div>
  <div class="name-tile"><span>Helen</span><span>&amp; Gavin</span></div>
  <div class="name-tile"><span>Helen</span><span>&amp; Gavin</span></div>

  <div class="name-tile"><span>Helen</span><span>&amp; Gavin</span></div>
  <div class="name-tile"><span>Helen</span><span>&amp; Gavin</span></div>
  <div class="hero-name"><span>Helen</span><span>&amp; Gavin</span></div>
  <div class="name-tile"><span>Helen</span><span>&amp; Gavin</span></div>
  <div class="name-tile"><span>Helen</span><span>&amp; Gavin</span></div>

  <div class="name-tile"><span>Helen</span><span>&amp; Gavin</span></div>
  <div class="name-tile"><span>Helen</span><span>&amp; Gavin</span></div>
  <div class="name-tile"><span>Helen</span><span>&amp; Gavin</span></div>
  <div class="name-tile"><span>Helen</span><span>&amp; Gavin</span></div>

  <div class="name-tile"><span>Helen</span><span>&amp; Gavin</span></div>
  <div class="name-tile"><span>Helen</span><span>&amp; Gavin</span></div>
  <div class="name-tile"><span>Helen</span><span>&amp; Gavin</span></div>
  <div class="name-tile"><span>Helen</span><span>&amp; Gavin</span></div>
  <div class="name-tile"><span>Helen</span><span>&amp; Gavin</span></div>
  <div class="name-tile"><span>Helen</span><span>&amp; Gavin</span></div>

  <div class="name-tile"><span>Helen</span><span>&amp; Gavin</span></div>
  <div class="name-tile"><span>Helen</span><span>&amp; Gavin</span></div>
  <div class="name-tile"><span>Helen</span><span>&amp; Gavin</span></div>
  <div class="name-tile"><span>Helen</span><span>&amp; Gavin</span></div>
  <div class="name-tile"><span>Helen</span><span>&amp; Gavin</span></div>
  <div class="name-tile"><span>Helen</span><span>&amp; Gavin</span></div>
</main>
</body>
</html>
```